Dietitian needs awesome business card

I need a contemporary design that's eye catching but professional.
My card is to given to doctors, specialists and patients alike.
I manage patients with chronic diseases
I have uploaded my logo and current business card, I would also like the other Certified Clinical Nutritionist logo incorporated into the design

Target Market(s)

Doctors, specialists and patients

Industry/Entity Type

Healthcare

Contact Information for Business Card

www.brightfieldnutrition.com.au
Ph: 0427 561 903
Fax: 6457 2183
email: marcus.k.diet@fernmail.com
Space on the back of the card with: Appointment date, Appointment time and appointment location

Font styles to use
Serif

Colors
fbee3e
876aae
ffc214

Requirements
Must have
• My Logo
• Certified Clinical Nutritionist Logo
• My 4 locations - Pinebrook Medical Centre, North Corrin Health, Hollis Medical, Ashcombe Doctors Surgery
Nice to have
• I like the colours in my current business card

```html
<!DOCTYPE html>
<html lang="en">
<head>
<meta charset="utf-8">
<title>Brightfield Nutrition &amp; Dietetics – Business Card</title>
<link rel="stylesheet" href="https://fonts.googleapis.com/css2?family=Lora:ital,wght@0,400;0,600;1,600&display=swap">
<style>
  :root {
    --backdrop: #e9e6e3;
    --card: #141414;
    --brand-blue: #2f5fc4;
    --brand-deep: #2a3fa8;
    --leaf-green: #8cc63f;
    --title-green: #a6d83a;
    --text-light: #e4e4e4;
    --text-muted: #bdbdbd;
    --badge-orange: #f47b20;
    --field-white: #ffffff;
  }
  * { box-sizing: border-box; margin: 0; padding: 0; }
  html, body {
    width: 1200px; height: 900px; overflow: hidden;
    background: var(--backdrop);
    font-family: "Lora", Georgia, serif;
  }
  .canvas { position: relative; width: 1200px; height: 900px; }

  .card {
    position: absolute;
    background: var(--card);
    box-shadow: 0 6px 18px rgba(0,0,0,0.25);
  }
  .card--front { left: 78px; top: 35px; width: 587px; height: 362px; }
  .card--back  { left: 388px; top: 505px; width: 567px; height: 352px; }

  /* brand lockup */
  .brand { position: absolute; display: flex; align-items: center; gap: 14px; }
  .brand__mark {
    width: 84px; height: 84px; border-radius: 50%;
    background: var(--brand-blue);
    flex: none;
  }
  .brand__name {
    color: var(--brand-blue);
    font-weight: 600;
    line-height: 1.05;
  }
  .brand__name .line1 { display: block; font-size: 38px; letter-spacing: 0.3px; }
  .brand__name .line2 { display: block; font-size: 18px; margin-top: 4px; }
  .card--front .brand { left: 45px; top: 20px; }
  .card--back .brand { left: 130px; top: 30px; }

  .badge {
    position: absolute; left: 482px; top: 58px;
    width: 46px; height: 50px;
    background: var(--badge-orange);
  }

  .holder {
    position: absolute; left: 60px; top: 162px;
    font-size: 20px; font-weight: 600; color: var(--brand-blue);
  }

  .contacts { position: absolute; left: 58px; top: 200px; list-style: none; }
  .contacts li {
    display: flex; align-items: center; gap: 9px;
    font-size: 15px; color: var(--text-light); height: 22px;
  }
  .contacts li.gap { margin-top: 3px; }
  .contacts svg { width: 12px; height: 12px; fill: var(--leaf-green); flex: none; }

  .locations {
    position: absolute; right: 40px; top: 170px;
    list-style: none; text-align: right;
  }
  .locations li {
    font-size: 12.5px; line-height: 21px; color: var(--text-muted);
  }

  .credentials {
    position: absolute; left: 58px; top: 310px;
    font-size: 13.5px; color: var(--title-green); text-transform: uppercase;
    white-space: nowrap;
  }

  /* appointment panel */
  .appointment { position: absolute; left: 108px; top: 195px; }
  .appointment__row { display: flex; align-items: center; height: 25px; }
  .appointment__label { width: 78px; font-size: 14px; color: var(--text-light); }
  .appointment__field {
    width: 282px; height: 21px;
    background: var(--field-white);
    border: 2px solid #000;
    outline: 1px solid #555;
  }
  .notice {
    position: absolute; left: 0; right: 0; top: 282px;
    text-align: center; font-size: 14px; font-style: italic; font-weight: 600;
    color: var(--brand-deep);
  }
</style>
</head>
<body>
<main class="canvas">

  <section class="card card--front" aria-label="Business card front">
    <div class="brand">
      <span class="brand__mark"></span>
      <span class="brand__name"><span class="line1">Brightfield</span><span class="line2">Nutrition &amp; Dietetics</span></span>
    </div>
    <span class="badge" aria-label="Accreditation badge"></span>

    <h1 class="holder">Marcus Kellaway</h1>

    <ul class="contacts">
      <li>
        <svg viewBox="0 0 12 12" aria-hidden="true"><path d="M2.5 0.8l2 2.2-1.1 1.5c.7 1.6 1.9 2.8 3.4 3.5L8.3 6.8l2.2 2-.9 2.2C5 10.8 1.2 7 .9 2.2z"/></svg>
        0427 561 903
      </li>
      <li>
        <svg viewBox="0 0 12 12" aria-hidden="true"><path d="M3 0h5v3H3zM1 4h10v6H1zM3 9h6v3H3z"/></svg>
        6457 2183
      </li>
      <li class="gap">
        <svg viewBox="0 0 12 12" aria-hidden="true"><path d="M1 2.5h10v7H1zM1.5 3l4.5 3.5L10.5 3" stroke="#141414" stroke-width="1"/></svg>
        marcus.k.diet@fernmail.com
      </li>
      <li>
        <svg viewBox="0 0 12 12" aria-hidden="true"><circle cx="6" cy="6" r="5.5"/><path d="M.5 6h11M6 .5c-2.5 3-2.5 8 0 11M6 .5c2.5 3 2.5 8 0 11" stroke="#141414" stroke-width="0.9" fill="none"/></svg>
        www.brightfieldnutrition.com.au
      </li>
    </ul>

    <ul class="locations" aria-label="Clinic locations">
      <li>Pinebrook Medical Centre</li>
      <li>North Corrin Health</li>
      <li>Hollis Medical</li>
      <li>Ashcombe Doctors Surgery</li>
    </ul>

    <p class="credentials">Certified Clinical Nutritionist, Nutritionist and Chef</p>
  </section>

  <section class="card card--back" aria-label="Business card back">
    <div class="brand">
      <span class="brand__mark"></span>
      <span class="brand__name"><span class="line1">Brightfield</span><span class="line2">Nutrition &amp; Dietetics</span></span>
    </div>

    <div class="appointment">
      <div class="appointment__row"><span class="appointment__label">Date:</span><span class="appointment__field"></span></div>
      <div class="appointment__row"><span class="appointment__label">Time:</span><span class="appointment__field"></span></div>
      <div class="appointment__row"><span class="appointment__label">Location:</span><span class="appointment__field"></span></div>
    </div>

    <p class="notice">If unable to keep appointment, kindly give 24hrs notice.</p>
  </section>

</main>
</body>
</html>
```